BrimFalcon Business Cards

We have a defined brand. Please visit our website to get a feel for the product and the color pallets. www.brimfalcon-example.com

We need an updated, world class business card design. (See the attached existing card design). Please utilize BOTH sides of the card as shown and be creative with the layout. I do want the horse head icon to be positioned as it is with the existing card.

The remainder of the layout can be customized and I also want it vertically oriented.

Attached are the logo files and please use the colors as follows:
Green - #A5CE39
Tan - #CDBD99
Black

Feel free to play with the colors.

```html
<!DOCTYPE html>
<html lang="en">
<head>
<meta charset="utf-8">
<title>BrimFalcon Business Cards</title>
<link href="https://fonts.googleapis.com/css2?family=Montserrat:wght@400;500;600&display=swap" rel="stylesheet">
<style>
  :root {
    --bg: #b9bcbd;
    --card: #2c2c2d;
    --card-edge: #a5ce39;
    --green: #a5ce39;
    --text: #e6e6e6;
    --muted: #8a8a8b;
    --emboss: #232324;
  }
  * { box-sizing: border-box; margin: 0; padding: 0; }
  html, body { width: 1200px; height: 880px; overflow: hidden; }
  body {
    background: var(--bg);
    font-family: "Montserrat", sans-serif;
    position: relative;
  }
  .card {
    position: absolute;
    background: var(--card);
    border-bottom: 6px solid var(--card-edge);
    box-shadow: 0 10px 24px rgba(0,0,0,0.25);
  }
  .card-front {
    left: 130px; top: 100px;
    width: 380px; height: 665px;
    display: flex; flex-direction: column; align-items: center;
    padding-top: 70px;
    text-align: center;
  }
  .brand-mark {
    width: 190px; height: 190px;
    border-radius: 50%;
    background: var(--emboss);
    box-shadow: inset 0 2px 4px rgba(0,0,0,0.5), 0 1px 0 rgba(255,255,255,0.05);
  }
  .brand-mark-label {
    margin-top: 14px;
    font-size: 15px; font-weight: 500;
    letter-spacing: 2px;
    color: var(--muted);
  }
  .person-name {
    margin-top: 34px;
    font-size: 26px; font-weight: 500;
    letter-spacing: 1.5px;
    color: var(--green);
    text-transform: uppercase;
  }
  .person-title {
    margin-top: 6px;
    font-size: 17px; font-weight: 400;
    color: var(--text);
  }
  .contact-icons {
    display: flex; gap: 12px;
    margin-top: 34px;
  }
  .contact-icon {
    width: 26px; height: 26px;
    border-radius: 50%;
    background: var(--green);
    display: flex; align-items: center; justify-content: center;
  }
  .contact-list {
    margin-top: 22px;
    list-style: none;
    font-size: 15px; line-height: 1.6;
    color: var(--text);
  }
  .divider {
    width: 60px; height: 2px;
    background: var(--green);
    margin: 26px 0;
  }
  .address {
    font-size: 15px; line-height: 1.6;
    color: var(--text);
    font-style: normal;
  }
  .card-back {
    left: 560px; top: 230px;
    width: 665px; height: 380px;
    display: flex; align-items: center; justify-content: center; gap: 22px;
    left: 540px;
  }
  .back-dot {
    width: 74px; height: 74px;
    border-radius: 50%;
    background: var(--emboss);
    box-shadow: inset 0 2px 4px rgba(0,0,0,0.5);
  }
  .back-wordmark {
    font-size: 52px; font-weight: 500;
    letter-spacing: 2px;
    color: var(--muted);
  }
</style>
</head>
<body>
  <section class="card card-back" aria-label="Card back">
    <span class="back-dot"></span>
    <span class="back-wordmark">BrimFalcon Labs</span>
  </section>

  <section class="card card-front" aria-label="Card front">
    <div class="brand-mark" role="img" aria-label="BrimFalcon brand mark area"></div>
    <div class="brand-mark-label">BrimFalcon</div>
    <h1 class="person-name">Dana Merrow</h1>
    <p class="person-title">President &amp; CEO</p>

    <div class="contact-icons">
      <span class="contact-icon">
        <svg width="14" height="14" viewBox="0 0 24 24" aria-hidden="true"><path d="M6.6 10.8a15 15 0 0 0 6.6 6.6l2.2-2.2a1 1 0 0 1 1-.25 11 11 0 0 0 3.6.6 1 1 0 0 1 1 1V20a1 1 0 0 1-1 1A17 17 0 0 1 3 4a1 1 0 0 1 1-1h3.5a1 1 0 0 1 1 1 11 11 0 0 0 .6 3.6 1 1 0 0 1-.25 1z" fill="#2c2c2d"/></svg>
      </span>
      <span class="contact-icon">
        <svg width="14" height="14" viewBox="0 0 24 24" aria-hidden="true"><rect x="3" y="6" width="18" height="12" rx="1" fill="none" stroke="#2c2c2d" stroke-width="2.2"/><path d="M3 7l9 6 9-6" fill="none" stroke="#2c2c2d" stroke-width="2.2"/></svg>
      </span>
      <span class="contact-icon">
        <svg width="14" height="14" viewBox="0 0 24 24" aria-hidden="true"><circle cx="12" cy="12" r="9" fill="none" stroke="#2c2c2d" stroke-width="2.2"/><path d="M3 12h18M12 3c3 3 3 15 0 18M12 3c-3 3-3 15 0 18" fill="none" stroke="#2c2c2d" stroke-width="1.8"/></svg>
      </span>
    </div>

    <ul class="contact-list">
      <li>555.010.4477</li>
      <li>dana@brimfalcon-example.com</li>
      <li>brimfalconlabs-example.com</li>
    </ul>

    <div class="divider"></div>

    <address class="address">Harlow Bay, Westland<br>Canada</address>
  </section>
</body>
</html>
```